Personal training and nutrition business needs business card design

We need a business card that outlays our services and invites potential customers to join our team and take the first step to a healthier and more enjoyable life. We cater for any level of fitness and specialize in weight loss and conditioning, strength training, muscle gain and strength endurance. Whether you are just starting off or need some help getting to the next level of your journey we are here to get the job done.
We specialize in one on one or one on two personal training sessions and each program will be custom made to suit individual fitness goals of our clients

```html
<!DOCTYPE html>
<html lang="en">
<head>
<meta charset="utf-8">
<title>Stride &amp; Pace — Business Card</title>
<link href="https://fonts.googleapis.com/css2?family=Roboto:wght@400;700;900&family=Oswald:wght@500&display=swap" rel="stylesheet">
<style>
  :root {
    --backdrop: #2a2a2a;
    --card: #f1f1f1;
    --card-edge: #e4e4e4;
    --ink: #111111;
    --text: #2f2f2f;
    --purple: #5e3a92;
    --violet: #7a4aa6;
    --pink: #a35ea3;
  }
  * { margin: 0; padding: 0; box-sizing: border-box; }
  html, body { width: 1200px; height: 1138px; overflow: hidden; }
  body { background: var(--backdrop); position: relative; font-family: "Roboto", sans-serif; }

  .card {
    position: absolute;
    background: linear-gradient(160deg, #f7f7f7, var(--card) 60%, var(--card-edge));
    border-radius: 14px;
    overflow: hidden;
    box-shadow: 0 6px 14px rgba(0,0,0,.45);
  }
  .card--front { left: 274px; top: 186px; width: 622px; height: 376px; }
  .card--back  { left: 276px; top: 608px; width: 618px; height: 374px; }

  /* front */
  .front-brand {
    position: absolute; left: 0; right: 0; top: 126px;
    display: flex; justify-content: center; align-items: center; gap: 14px;
  }
  .brand-dot { width: 30px; height: 30px; background: var(--violet); }
  .brand-name {
    font-family: "Roboto", sans-serif; font-weight: 900; color: var(--ink);
    font-size: 46px; letter-spacing: 1px; text-transform: uppercase;
  }
  .front-tagline {
    position: absolute; left: 0; right: 0; top: 252px; text-align: center;
    font-family: "Oswald", sans-serif; font-weight: 500; font-size: 14px;
    letter-spacing: 1.4px; color: var(--violet);
  }
  .front-web {
    position: absolute; left: 0; right: 0; top: 322px;
    display: flex; justify-content: center; align-items: center; gap: 18px;
    font-size: 16px; color: var(--text);
  }
  .front-web .rule { width: 72px; height: 2px; background: var(--ink); }
  .accent { color: var(--violet); }
  .front-band {
    position: absolute; left: 0; right: 0; bottom: 0; height: 11px;
    background: linear-gradient(90deg, var(--pink), var(--purple));
  }

  /* back */
  .back-brand {
    position: absolute; left: 26px; top: 56px;
    display: flex; align-items: center; gap: 16px;
  }
  .back-brand .brand-dot { width: 36px; height: 36px; }
  .back-brand .brand-name { font-size: 40px; }
  .person { position: absolute; left: 34px; top: 198px; }
  .person-name {
    font-weight: 900; font-size: 24px; letter-spacing: 1px; color: var(--violet);
    text-transform: uppercase;
  }
  .person-role { font-size: 16px; color: var(--text); margin-top: 4px; }
  .address { position: absolute; left: 34px; top: 284px; font-size: 16px; line-height: 24px; color: var(--text); }
  .contacts { position: absolute; left: 338px; top: 203px; list-style: none; }
  .contacts li { display: flex; align-items: center; gap: 16px; font-size: 16px; line-height: 24px; color: var(--text); }
  .contacts svg { width: 14px; height: 14px; fill: var(--violet); }
  .back-bands { position: absolute; left: 0; bottom: 0; width: 618px; height: 46px; }
  .services {
    position: absolute; right: 20px; bottom: 12px;
    font-size: 16px; color: #fff; letter-spacing: .2px;
  }
</style>
</head>
<body>

<section class="card card--front" aria-label="Card front">
  <div class="front-brand">
    <span class="brand-dot"></span>
    <span class="brand-name">Stride &amp; Pace</span>
  </div>
  <p class="front-tagline">PERSONAL TRAINING.&nbsp; NUTRITION. MOTIVATION</p>
  <p class="front-web"><span class="rule"></span>www.<span class="accent">strideandpace</span>.com<span class="rule"></span></p>
  <div class="front-band"></div>
</section>

<section class="card card--back" aria-label="Card back">
  <div class="back-brand">
    <span class="brand-dot"></span>
    <span class="brand-name">Stride &amp; Pace</span>
  </div>

  <div class="person">
    <p class="person-name">Dana Mercer</p>
    <p class="person-role">Personal Trainer</p>
  </div>

  <p class="address">1820 Maple Ridge Road<br>Cedar Falls Texas 75112</p>

  <ul class="contacts">
    <li><svg viewBox="0 0 16 16"><path d="M3 2h3l1.5 3.5-2 1.3a8 8 0 0 0 3.7 3.7l1.3-2L14 10v3a1 1 0 0 1-1 1A11 11 0 0 1 2 3a1 1 0 0 1 1-1z"/></svg>+1 (555) 210-4477</li>
    <li><svg viewBox="0 0 16 16"><path d="M1 3h14v10H1z M2 4l6 5 6-5" fill="none" stroke="#7a4aa6" stroke-width="1.6"/></svg>dana@strideandpace.com</li>
    <li><svg viewBox="0 0 16 16"><circle cx="8" cy="8" r="6.5" fill="none" stroke="#7a4aa6" stroke-width="1.4"/><path d="M1.5 8h13M8 1.5c-3 3.5-3 9.5 0 13M8 1.5c3 3.5 3 9.5 0 13" fill="none" stroke="#7a4aa6" stroke-width="1.2"/></svg>www.<span class="accent">strideandpace</span>.com</li>
  </ul>

  <svg class="back-bands" viewBox="0 0 618 46" preserveAspectRatio="none" aria-hidden="true">
    <defs>
      <linearGradient id="pinkBand" x1="0" x2="1">
        <stop offset="0" stop-color="#a35ea3"/>
        <stop offset="1" stop-color="#8a4f9e"/>
      </linearGradient>
    </defs>
    <rect x="0" y="31" width="280" height="15" fill="url(#pinkBand)"/>
    <path d="M276 0 H618 V46 H252 Z" fill="#5e3a92"/>
  </svg>
  <p class="services">Personal Training | Nutrition | Motivation</p>
</section>

</body>
</html>
```